Dental specialist needs a sharp looking letterhead

I am looking for a letterhead to be used to send letters and communication between myself (a dental specialist) and other dentists.
My office is a state of the art dental specialty office.
I need to letterhead to also state:
Bertram L. Oswick DDS
2748 Tollard Avenue, Suite K
West Tollard, NY 14391
(716)392-5061
fax: (716)392-5087
oswickroot.com (**this email address may change)

i included my logo designs.
thank you

Target Market(s)

dentists

Industry/Entity Type

Communication

Requirements
Must have
• the included logo, whether the vertical or horizontal versions

```html
<!DOCTYPE html>
<html lang="en">
<head>
<meta charset="utf-8">
<title>Meridian Endodontics P.C. — Letterhead</title>
<link rel="stylesheet" href="https://fonts.googleapis.com/css2?family=Arvo:wght@400;700&family=Open+Sans:wght@400;600&display=swap">
<style>
  :root {
    --backdrop: #ececec;
    --paper: #ffffff;
    --brand-blue: #3d93d2;
    --brand-green: #6cae2f;
    --ink-black: #111111;
    --ink-dark: #1c1c1c;
    --text-light: #ffffff;
  }
  * { box-sizing: border-box; margin: 0; padding: 0; }
  html, body {
    width: 1200px; height: 968px; overflow: hidden;
    background: var(--backdrop);
  }
  .letterhead {
    position: absolute;
    left: 270px; top: 57px;
    width: 660px; height: 854px;
    background: var(--paper);
    box-shadow: 0 2px 10px rgba(0,0,0,0.08);
  }
  .practice-name {
    position: absolute;
    left: 36px; top: 44px;
    display: flex; align-items: center; gap: 10px;
    font-family: "Arvo", serif;
    color: var(--ink-dark);
  }
  .practice-name .mark-dot {
    width: 30px; height: 30px; border-radius: 50%;
    background: var(--brand-blue);
    flex: none;
  }
  .practice-name .wording {
    border-left: 1px solid var(--ink-dark);
    padding-left: 10px;
    line-height: 1;
  }
  .practice-name .title {
    display: block;
    font-size: 24px; font-weight: 700; letter-spacing: 0.5px;
  }
  .practice-name .subtitle {
    display: block;
    font-size: 10px; font-weight: 700; letter-spacing: 2.6px;
    margin-top: 3px;
  }
  .contact-block {
    position: absolute;
    left: 262px; right: 0; top: 38px;
    font-family: "Open Sans", sans-serif;
  }
  .doctor-line {
    display: flex; align-items: flex-end; gap: 6px;
  }
  .doctor-name {
    font-family: "Arvo", serif;
    font-size: 12px; color: var(--brand-blue);
    white-space: nowrap; line-height: 1.2;
  }
  .doctor-line .blue-band {
    flex: 1; height: 7px; background: var(--brand-blue);
    margin-bottom: 2px;
  }
  .band {
    display: flex; align-items: center; gap: 12px;
    height: 16px; padding-left: 6px;
    color: var(--text-light);
    font-size: 8.5px; white-space: nowrap;
  }
  .band-green { background: var(--brand-green); margin-top: 1px; }
  .band-black { background: var(--ink-black); }
  .band .item { display: flex; align-items: center; gap: 4px; }
  .band svg { width: 9px; height: 9px; flex: none; }
</style>
</head>
<body>
  <main class="letterhead">
    <header>
      <div class="practice-name">
        <span class="mark-dot"></span>
        <span class="wording">
          <span class="title">MERIDIAN</span>
          <span class="subtitle">Endodontics P.C.</span>
        </span>
      </div>

      <div class="contact-block">
        <div class="doctor-line">
          <span class="doctor-name">Bertram L. Oswick DDS</span>
          <span class="blue-band"></span>
        </div>
        <div class="band band-green">
          <span class="item">
            <svg viewBox="0 0 10 10"><circle cx="5" cy="5" r="5" fill="#fff"/><path d="M3 2.5 L4 2.5 L4.6 4 L4 4.5 Q4.6 5.6 5.5 6 L6 5.4 L7.5 6 L7.5 7 Q5.5 7.5 3.8 5.6 Q2.6 4.2 3 2.5Z" fill="#6cae2f"/></svg>
            (716)392-5061
          </span>
          <span class="item">
            <svg viewBox="0 0 10 10"><circle cx="5" cy="5" r="5" fill="#fff"/><rect x="3" y="4" width="4" height="3" fill="#6cae2f"/><rect x="3.6" y="2.6" width="2.8" height="1.6" fill="#6cae2f"/></svg>
            (716)392-5087
          </span>
          <span class="item">
            <svg viewBox="0 0 10 10"><circle cx="5" cy="5" r="5" fill="#fff"/><rect x="2.6" y="3.2" width="4.8" height="3.6" fill="#6cae2f"/><path d="M2.6 3.2 L5 5.2 L7.4 3.2" stroke="#fff" stroke-width="0.6" fill="none"/></svg>
            bertram@oswickroot.com
          </span>
        </div>
        <div class="band band-black">
          <span class="item">
            <svg viewBox="0 0 10 10"><circle cx="5" cy="5" r="5" fill="#fff"/><path d="M5 2 Q7 2 7 4 Q7 5.5 5 8 Q3 5.5 3 4 Q3 2 5 2Z" fill="#111"/><circle cx="5" cy="4" r="0.8" fill="#fff"/></svg>
            2748 Tollard Avenue, Suite K, West Tollard, NY 14391
          </span>
        </div>
      </div>
    </header>
  </main>
</body>
</html>
```